Lunelle Rosa Hair Fancy Business Card’s

I want my business cards to be elite, original and very classy. I want the business cards to match the colors of my logo and to match the design posted. I would love the design of the picture I posted

I want the card all white .
The dripping on the top of the card I want it to match the pink color in my logo that’s also posted .
I need my logo on the business card !
I need my Instagram- @lunelle.rosa.hair__
And my phone number - 555 207 3962

Target Market(s)

My target market is young woman age 23 to older woman to the age of 65
I want both older and younger women to love my design . I don’t want any cheap looking business cards

Industry/Entity Type

Hair And Beauty

Contact Information for Business Card

Add my logo
Add my Instagram- @lunelle.rosa.hair__
My number - 555 207 3962
My website- www.lunellerosahair.example

Font styles to use
Serif
Script

Colors
ffffff
e667a6
e34298

Requirements
Must have
• The business cards must have my logo, my number , my website, and my Instagram!
Nice to have
• Nice to have glitter words that match my logo
• The business cards must look classy and mature
• I want them to be very unique!!
Should not have
• Should not have any colors that doesn’t match my logo ! This is very important! Please

```html
<!DOCTYPE html>
<html lang="en">
<head>
<meta charset="utf-8">
<title>Lunelle Rosa Hair — Business Card</title>
<link rel="stylesheet" href="https://fonts.googleapis.com/css2?family=Lato:wght@400;700&display=swap">
<style>
  :root {
    --canvas-bg: #ecebea;
    --card-white: #ffffff;
    --brand-pink: #e34298;
    --brand-pink-soft: #e667a6;
    --text-grey: #6b6b6b;
    --glitter-dark-1: #3a3a3c;
    --glitter-dark-2: #5e5e61;
    --glitter-light-1: #9c9ea1;
    --glitter-light-2: #d7d8da;
    --card-shadow: 0 10px 28px rgba(0,0,0,0.18);
  }
  * { box-sizing: border-box; margin: 0; padding: 0; }
  html, body {
    width: 1200px; height: 900px; overflow: hidden;
    background: var(--canvas-bg);
    font-family: "Lato", Arial, sans-serif;
  }
  .canvas { position: relative; width: 1200px; height: 900px; }
  .card {
    position: absolute; width: 700px; height: 400px;
    left: 250px; overflow: hidden; border-radius: 4px;
    box-shadow: var(--card-shadow);
  }
  .card--back { top: 40px; }
  .card--front { top: 470px; background: var(--card-white); }

  .glitter-back {
    position: absolute; inset: 0;
    background: radial-gradient(ellipse at 40% 40%, var(--glitter-dark-2), var(--glitter-dark-1) 75%);
  }
  .brand-name {
    font-family: "Lato", Arial, sans-serif;
    font-weight: 700; color: var(--brand-pink);
    letter-spacing: 0.02em; white-space: nowrap;
  }
  .card--back .brand-name {
    position: absolute; left: 0; right: 0; top: 170px;
    text-align: center; font-size: 46px; color: var(--card-white);
  }

  .card-wave { position: absolute; inset: 0; width: 700px; height: 400px; }
  .wave-band { fill: var(--brand-pink); }
  .glitter-stop-light { stop-color: var(--glitter-light-2); }
  .glitter-stop-mid { stop-color: var(--glitter-light-1); }

  .contact-list { position: absolute; left: 62px; top: 0; list-style: none; }
  .contact-item {
    position: absolute; left: 0; display: flex; align-items: center;
    gap: 12px; font-size: 22px; line-height: 1; color: var(--text-grey); white-space: nowrap;
  }
  .contact-item--phone { top: 110px; }
  .contact-item--web { top: 148px; }
  .contact-item--social { top: 216px; left: 30px; }
  .contact-icon { width: 24px; height: 24px; flex: none; }

  .card--front .brand-name {
    position: absolute; right: 40px; top: 92px;
    font-size: 32px; text-align: right;
  }
</style>
</head>
<body>
<main class="canvas">

  <section class="card card--back" aria-label="Card back">
    <div class="glitter-back" role="img" aria-label="Dark silver glitter texture"></div>
    <p class="brand-name">Lunelle Rosa Hair</p>
  </section>

  <section class="card card--front" aria-label="Card front">
    <svg class="card-wave" viewBox="0 0 700 400">
      <defs>
        <linearGradient id="glitterFill" x1="0" y1="0" x2="1" y2="1">
          <stop offset="0" class="glitter-stop-light"/>
          <stop offset="0.5" class="glitter-stop-mid"/>
          <stop offset="1" class="glitter-stop-light"/>
        </linearGradient>
      </defs>
      <path class="wave-band"
            d="M0 296 C200 318 370 268 520 198 C400 270 220 330 0 326 Z"/>
      <path class="wave-glitter" role="img" aria-label="Silver glitter texture"
            fill="url(#glitterFill)"
            d="M0 338 C210 344 390 290 520 210 C590 168 650 150 700 146 L700 400 L0 400 Z"/>
    </svg>

    <ul class="contact-list">
      <li class="contact-item contact-item--phone">
        <svg class="contact-icon" viewBox="0 0 24 24">
          <circle cx="12" cy="12" r="10.5" fill="none" stroke="#e34298" stroke-width="2"/>
          <path d="M8.2 7.2l1.8-.4 1.2 2.6-1.2 1c.6 1.3 1.6 2.3 2.9 2.9l1-1.2 2.6 1.2-.4 1.8c-.2.6-.8 1-1.5.9-3.7-.5-6.7-3.5-7.2-7.2-.1-.7.3-1.3.8-1.6z" fill="#e34298"/>
        </svg>
        <span>555 207 3962</span>
      </li>
      <li class="contact-item contact-item--web">
        <svg class="contact-icon" viewBox="0 0 24 24">
          <circle cx="12" cy="12" r="11" fill="#e34298"/>
          <g fill="none" stroke="#fff" stroke-width="1.3">
            <circle cx="12" cy="12" r="7.5"/>
            <ellipse cx="12" cy="12" rx="3.2" ry="7.5"/>
            <path d="M4.5 12h15M6 8h12M6 16h12"/>
          </g>
        </svg>
        <span>www.lunellerosahair.example</span>
      </li>
      <li class="contact-item contact-item--social">
        <svg class="contact-icon" viewBox="0 0 24 24">
          <circle cx="12" cy="12" r="11" fill="#e34298"/>
        </svg>
        <span>@lunelle.rosa.hair__</span>
      </li>
    </ul>

    <p class="brand-name">Lunelle Rosa Hair</p>
  </section>

</main>
</body>
</html>
```